creation of a business card design for a company specializing in the creation...

I would like to create a design for a professional business card on a black background and with the company's colors (I am attaching some files: including the logo in horizontal and centered format, I am also attaching a recent project design a T-shirt, this is the one I chose to give you an idea of my preferences.

we are in the process of developing a new website design, it is still in the development phase but it can be viewed at the following address: www.vantrelmo.be to give you other ideas about the company
you will see for yourself the subject of my main activity: company specializing in the construction of stairs

I would like a business card that stands out from the rest with a unique design

here is the informations
Name: Lucien Barthel
Function: Manager
Address: Rue Moulinet du Parc 42
7180 Marvelle
telephone: +32 468 219 804
email: info@rx7p.be
website: rx7p. be
social networks: Facebook, YouTube, TikTok, Instagram

Target Market(s)

customer who wants to have a beautiful staircase built

Industry/Entity Type

contruction d'escalier

Contact Information for Business Card

Adresse. Numero de telephone, site web, le texte : "Createur d'escalier", logo recto-verso, icone des reseaux sociaux

Requirements
Must have
• the mention: Stair creator
Nice to have
• an illustration of a designer staircase
Should not have
• do not distort the logo

```html
<!DOCTYPE html>
<html lang="en">
<head>
<meta charset="utf-8">
<title>RX7P business card</title>
<link rel="stylesheet" href="https://fonts.googleapis.com/css2?family=Montserrat:wght@300;400;500;700&display=swap">
<style>
  :root {
    --page: #2a2b2e;
    --card: #131314;
    --white: #f2f2f2;
    --blue: #6f9fc4;
    --blue-light: #9ec0db;
    --grey: #d6d6d6;
  }
  * { box-sizing: border-box; margin: 0; padding: 0; }
  html, body { width: 1200px; height: 900px; overflow: hidden; }
  body {
    background: var(--page);
    font-family: "Montserrat", Arial, sans-serif;
    position: relative;
  }
  .card {
    position: absolute;
    top: 293px;
    width: 550px;
    height: 314px;
    background: var(--card);
    border-radius: 18px;
    box-shadow: 0 14px 34px rgba(0,0,0,0.45);
    overflow: hidden;
  }
  .card--front { left: 35px; }
  .card--back { left: 615px; }

  .brand { position: absolute; display: flex; flex-direction: column; }
  .brand__row { display: flex; align-items: center; }
  .brand__mark { background: var(--blue); flex: none; }
  .brand__name {
    color: var(--white);
    font-weight: 300;
    line-height: 1;
  }
  .brand__tagline {
    color: var(--blue-light);
    font-weight: 400;
    text-transform: uppercase;
    white-space: nowrap;
  }

  .card--front .brand { left: 110px; top: 104px; }
  .card--front .brand__mark { width: 54px; height: 54px; margin-right: 24px; }
  .card--front .brand__name { font-size: 78px; letter-spacing: 10px; }
  .card--front .brand__tagline { font-size: 12px; letter-spacing: 6.4px; margin: 12px 0 0 80px; }

  .card--back .brand { left: 34px; top: 196px; }
  .card--back .brand__mark { width: 26px; height: 26px; margin-right: 12px; }
  .card--back .brand__name { font-size: 38px; letter-spacing: 5px; }
  .card--back .brand__tagline { font-size: 6.5px; letter-spacing: 3.2px; margin: 6px 0 0 38px; }

  .divider {
    position: absolute;
    left: 258px; top: 46px;
    width: 1px; height: 162px;
    background: var(--blue);
  }
  .contact { position: absolute; left: 282px; top: 44px; color: var(--grey); }
  .contact__name { color: var(--blue); font-weight: 700; font-size: 21px; }
  .contact__role { font-size: 12px; font-weight: 400; margin-top: 2px; }
  .contact__address { font-size: 12px; line-height: 1.35; margin-top: 18px; }
  .contact__list { list-style: none; margin-top: 16px; font-size: 12px; }
  .contact__list li { display: flex; align-items: center; gap: 9px; line-height: 1.6; }
  .contact__list svg { width: 11px; height: 11px; flex: none; }

  .social { position: absolute; left: 318px; top: 256px; display: flex; gap: 12px; }
  .social__dot { width: 15px; height: 15px; border-radius: 4px; background: var(--blue); }
</style>
</head>
<body>
  <section class="card card--front" aria-label="Card front">
    <div class="brand">
      <div class="brand__row">
        <span class="brand__mark"></span>
        <span class="brand__name">RX7P</span>
      </div>
      <span class="brand__tagline">Bespoke Stairways</span>
    </div>
  </section>

  <section class="card card--back" aria-label="Card back">
    <div class="brand">
      <div class="brand__row">
        <span class="brand__mark"></span>
        <span class="brand__name">RX7P</span>
      </div>
      <span class="brand__tagline">Bespoke Stairways</span>
    </div>

    <div class="divider"></div>

    <div class="contact">
      <p class="contact__name">Lucien Barthel</p>
      <p class="contact__role">Manager</p>
      <p class="contact__address">Rue Moulinet du Parc 42<br>7180 Marvelle</p>
      <ul class="contact__list">
        <li>
          <svg viewBox="0 0 16 16" aria-hidden="true"><path fill="#6f9fc4" d="M3.6 1.5l2.3 2.6-1.3 1.8c.9 2 2.4 3.6 4.5 4.5l1.8-1.3 2.6 2.3-1.4 2.1C6.6 13.8 2.2 9.4 1.5 3z"/></svg>
          <span>+32 468 219 804</span>
        </li>
        <li>
          <svg viewBox="0 0 16 16" aria-hidden="true"><rect x="1" y="3" width="14" height="10" rx="1" fill="#6f9fc4"/><path d="M1.5 3.8L8 9l6.5-5.2" stroke="#131314" stroke-width="1.3" fill="none"/></svg>
          <span>info@rx7p.be</span>
        </li>
        <li>
          <svg viewBox="0 0 16 16" aria-hidden="true"><circle cx="8" cy="8" r="6.5" fill="none" stroke="#6f9fc4" stroke-width="1.6"/><path d="M1.5 8h13M8 1.5c-3 3.5-3 9.5 0 13M8 1.5c3 3.5 3 9.5 0 13" stroke="#6f9fc4" stroke-width="1.2" fill="none"/></svg>
          <span>www.rx7p.be</span>
        </li>
      </ul>
    </div>

    <div class="social" aria-label="Social networks">
      <span class="social__dot"></span>
      <span class="social__dot"></span>
      <span class="social__dot"></span>
      <span class="social__dot"></span>
    </div>
  </section>
</body>
</html>
```